Business Card Design for a Software Startup

We'd like to have a business card design. We already have a logo. Basically what we need is a clean design with name, address, cellphone and phone numbers, e-mail and web site address (front) and a space on the back with our logo with the company name on the right side and some texts on the bottom.
We are a development and consulting company in Brazil with highly qualified team of professionals in Java, iOS and Android development and consulting.

Target Market(s)

CIO, IT managers of mid to big size companies

Industry/Entity Type

Business

```html
<!DOCTYPE html>
<html lang="en">
<head>
<meta charset="UTF-8">
<title>VANTIX Business Card</title>
<link href="https://fonts.googleapis.com/css2?family=Open+Sans:wght@400;700&display=swap" rel="stylesheet">
<style>
  :root {
    --navy: #123a66;
    --blue: #1b6fae;
    --ink: #333a42;
    --paper: #ffffff;
    --backdrop: #e9ebee;
  }
  * { margin: 0; padding: 0; box-sizing: border-box; }
  html, body {
    width: 1200px;
    height: 720px;
    overflow: hidden;
    background: var(--backdrop);
    font-family: "Open Sans", Arial, sans-serif;
  }
  .canvas {
    position: relative;
    width: 1200px;
    height: 720px;
  }
  .card {
    position: absolute;
    top: 205px;
    width: 540px;
    height: 309px;
    background: var(--paper);
    box-shadow: 0 6px 18px rgba(0, 0, 0, 0.12);
  }
  .card--front { left: 40px; }
  .card--back { left: 620px; }

  /* Front */
  .brand-square {
    position: absolute;
    left: 42px;
    top: 72px;
    width: 160px;
    height: 160px;
    border-radius: 18px;
    background: var(--blue);
  }
  .wordmark {
    font-weight: 700;
    color: var(--navy);
    letter-spacing: 1px;
    line-height: 1;
  }
  .card--front .wordmark {
    position: absolute;
    left: 248px;
    top: 24px;
    font-size: 50px;
  }
  .details {
    position: absolute;
    left: 248px;
    top: 100px;
    color: var(--ink);
  }
  .person {
    font-size: 19px;
    color: var(--navy);
    font-weight: 700;
    margin-bottom: 8px;
  }
  .person .title {
    font-weight: 400;
    font-size: 16px;
    color: var(--ink);
  }
  .address {
    font-size: 12.5px;
    line-height: 1.35;
    margin-bottom: 12px;
  }
  .contact-list {
    list-style: none;
    font-size: 13px;
    line-height: 1.65;
  }
  .contact-list .label {
    display: inline-block;
    width: 22px;
    color: var(--blue);
  }

  /* Back */
  .back-lockup {
    position: absolute;
    left: 50%;
    top: 108px;
    transform: translateX(-50%);
    display: flex;
    align-items: center;
    gap: 16px;
  }
  .back-lockup .brand-square {
    position: static;
    width: 74px;
    height: 74px;
    border-radius: 10px;
  }
  .card--back .wordmark { font-size: 66px; }
  .web-address {
    position: absolute;
    left: 0;
    right: 0;
    bottom: 38px;
    text-align: center;
    font-size: 15px;
    font-weight: 700;
    letter-spacing: 6px;
    color: var(--ink);
  }
  .web-address .domain { color: var(--blue); }
</style>
</head>
<body>
<main class="canvas">
  <section class="card card--front" aria-label="Business card front">
    <div class="brand-square"></div>
    <div class="wordmark">VANTIX</div>
    <div class="details">
      <p class="person">Your Name, <span class="title">Title</span></p>
      <p class="address">Door No. Street Name<br>City Name, State, Zip Code</p>
      <ul class="contact-list">
        <li><span class="label">P:</span>123-456-7890</li>
        <li><span class="label">C:</span>123-456-7890</li>
        <li><span class="label">E:</span>yourname@vantix.com</li>
        <li><span class="label">W:</span>www.vantix.com</li>
      </ul>
    </div>
  </section>

  <section class="card card--back" aria-label="Business card back">
    <div class="back-lockup">
      <div class="brand-square"></div>
      <div class="wordmark">VANTIX</div>
    </div>
    <p class="web-address">www.<span class="domain">vantix</span>.com</p>
  </section>
</main>
</body>
</html>
```